Double Sided Flyer for 3D printing services company

We need a nice balanced flyer for our corporate handout. The attached is for concept only and not the final design. We think the attached examples have elements that balance nicely but the graphics are not good. We are attaching the logo from the corporate office for our new logo. We will add the company information after the final design is selected for web address, phone, mailing etc. Please leave room for that information in the design. Please ask any questions prior to submission. Our main focus is printing RUBBER 3D Parts and not plastic parts. The images selected should be focused on that. We also need to ensure the images are approved for use in a corporate flyer for content.

```html
<!DOCTYPE html>
<html lang="en">
<head>
<meta charset="utf-8">
<title>Corvane – Double Sided Flyer</title>
<link rel="stylesheet" href="https://fonts.googleapis.com/css2?family=Barlow+Condensed:ital,wght@1,800;1,900&family=Poppins:wght@300;400;500;600;700&display=swap">
<style>
  :root{
    --stage:#b4b4b4;
    --ink:#2a2a2b;
    --ink-deep:#1f1f20;
    --orange:#f27a1a;
    --orange-deep:#d9471f;
    --grey:#8a8a8a;
    --grey-light:#c9c9c9;
    --paper:#ffffff;
    --text-light:#e9e9e9;
  }
  *{box-sizing:border-box;margin:0;padding:0}
  html,body{width:720px;height:1200px;overflow:hidden}
  body{background:var(--stage);font-family:"Poppins",sans-serif;position:relative}
  .flyer{position:absolute;left:150px;width:420px;height:594px;overflow:hidden;box-shadow:4px 6px 14px rgba(0,0,0,.35)}
  .flyer--front{top:4px;background:var(--ink)}
  .flyer--back{top:602px;background:var(--paper)}
  .abs{position:absolute;white-space:nowrap}
  .display{font-family:"Barlow Condensed",sans-serif;font-style:italic;font-weight:900;text-transform:uppercase;line-height:1}

  /* brand */
  .brand{right:30px;top:26px;display:flex;flex-direction:column;align-items:flex-end}
  .brand__row{display:flex;align-items:center;gap:6px}
  .brand__dot{width:24px;height:24px;border-radius:50%;background:var(--orange)}
  .brand__name{font-family:"Poppins",sans-serif;font-weight:700;font-size:24px;color:#fff;letter-spacing:.5px;line-height:1}
  .brand__tag{font-size:6.2px;color:#fff;letter-spacing:1.2px;margin-top:2px}

  /* front headline */
  .front-lower{left:0;top:385px;width:420px;height:209px;background:linear-gradient(180deg,rgba(0,0,0,0) 0,var(--ink-deep) 30%,var(--ink) 100%)}
  .trusted{left:39px;top:410px;width:186px;font-weight:300;font-size:10px;letter-spacing:2.6px;line-height:14px;color:#fff}
  .premium{left:232px;top:405px;width:152px;height:20px;background:var(--orange-deep);color:#fff;font-weight:700;font-size:15px;text-align:center;line-height:21px}
  .headline{left:36px;top:425px;font-size:44px;color:#fff;letter-spacing:.3px}
  .headline span{color:var(--orange)}
  .expertise{left:34px;top:479px;font-size:13.5px;line-height:14.5px;color:var(--orange)}
  .expertise b{color:#fff;font-weight:900}
  .feature{display:flex;align-items:center;gap:8px;color:var(--text-light);font-size:7.4px;line-height:9px}
  .feature svg{flex:none}

  /* footer */
  .footer{left:34px;width:200px;display:flex;align-items:center;gap:8px;font-size:8.6px}
  .footer .sep{width:1px;height:11px;background:var(--grey)}
  .footer .ic{display:inline-flex;align-items:center;gap:3px}
  .web{right:0;height:19px;width:196px;background:var(--grey);color:#fff;font-weight:600;font-size:12px;letter-spacing:3px;line-height:19px;padding-left:17px}

  /* back */
  .back-top{left:0;top:0;width:420px;height:354px;background:linear-gradient(100deg,#333334 0%,#272728 55%,#3a3a3b 100%)}
  .quick{left:34px;top:30px;font-size:29px;color:#fff}
  .quick span{color:var(--orange)}
  .redefine{left:34px;top:70px;font-size:16.5px;line-height:20px;color:#fff}
  .redefine b{font-weight:600}
  .need{left:204px;top:92px;font-size:15px;font-weight:700;color:var(--orange)}
  .need-sub{left:204px;top:114px;font-size:11px;color:#fff;line-height:13.5px}
  .steps{left:34px;top:153px;width:116px}
  .step{display:flex;gap:8px;align-items:flex-start;padding:5px 0;border-bottom:1px dotted #6a6a6a;color:#fff;font-size:8.3px;line-height:10.5px}
  .step:last-child{border-bottom:0}
  .step__num{font-family:"Barlow Condensed",sans-serif;font-style:italic;font-weight:900;color:var(--orange);font-size:26px;line-height:24px;width:12px}
  .confirm{left:30px;top:293px;width:110px;white-space:normal;border-left:1.5px solid var(--orange);padding-left:7px;color:#fff;font-weight:700;font-size:7.6px;line-height:9.8px}
  .product{width:82px;text-align:center;top:164px;white-space:normal}
  .product__photo{width:74px;height:74px;margin:0 auto;border-radius:50%;border:3px solid var(--orange-deep);box-shadow:-3px 3px 0 #9a9a9a}
  .product__name{margin-top:6px;font-size:13px;color:var(--orange)}
  .product__text{margin-top:3px;font-size:5.4px;line-height:6.6px;color:#fff}
  .benefits-band{left:140px;top:321px;width:280px;height:34px;background:linear-gradient(90deg,var(--orange),var(--orange-deep));clip-path:polygon(12px 0,100% 0,100% 100%,0 100%)}
  .benefits-title{left:164px;top:326px;font-size:22px;color:#fff}
  .benefit{left:34px;width:356px;height:29px}
  .benefit__label{position:absolute;left:0;top:0;width:190px;height:29px;background:linear-gradient(90deg,var(--orange),var(--orange-deep));color:#fff;font-weight:600;font-size:8px;line-height:29px;padding-left:22px}
  .benefit__desc{position:absolute;left:186px;top:0;width:170px;height:29px;white-space:normal;background:#cdcdcd;clip-path:polygon(0 0,100% 0,97% 100%,0 100%);font-size:5.2px;line-height:6.6px;color:#333;padding:4px 10px 0 26px}
  .benefit__icon{position:absolute;left:166px;top:-2px;width:33px;height:33px;border-radius:50%;background:#fff;display:flex;align-items:center;justify-content:center;box-shadow:0 0 0 2px #e6e6e6}
  .back-footer{color:#333}
</style>
</head>
<body>

<!-- FRONT SIDE -->
<section class="flyer flyer--front" aria-label="Flyer front">
  <svg class="abs" style="left:0;top:0" width="420" height="400" viewBox="0 0 420 400">
    <defs>
      <linearGradient id="metal" x1="0" y1="0" x2="1" y2="1">
        <stop offset="0" stop-color="#3b4048"/>
        <stop offset=".45" stop-color="#b9c2cc"/>
        <stop offset=".7" stop-color="#6f7884"/>
        <stop offset="1" stop-color="#d7dde3"/>
      </linearGradient>
      <linearGradient id="ring" x1="0" y1="0" x2="0" y2="1">
        <stop offset="0" stop-color="#4a4a4b"/>
        <stop offset="1" stop-color="#9a9a9b"/>
      </linearGradient>
    </defs>
    <ellipse cx="150" cy="210" rx="258" ry="175" fill="url(#ring)"/>
    <ellipse cx="150" cy="195" rx="250" ry="160" fill="var(--orange-deep)"/>
    <ellipse cx="150" cy="205" rx="238" ry="152" fill="#fff"/>
    <g role="img" aria-label="Close-up photograph of chrome hydraulic hose fittings">
      <ellipse cx="148" cy="205" rx="233" ry="147" fill="url(#metal)"/>
    </g>
    <g fill="#fff">
      <circle cx="95" cy="15" r="3"/>
      <circle cx="323" cy="168" r="3"/>
      <circle cx="350" cy="267" r="7"/>
      <circle cx="315" cy="340" r="10"/>
      <circle cx="225" cy="380" r="12"/>
      <circle cx="55" cy="330" r="13"/>
    </g>
  </svg>
  <div class="abs front-lower"></div>

  <div class="abs brand">
    <div class="brand__row"><span class="brand__dot"></span><span class="brand__name">CORVANE</span></div>
    <div class="brand__tag">SEALS·GASKETS·HOSES</div>
  </div>

  <div class="abs trusted">YOUR TRUSTED SOURCE</div>
  <div class="abs premium">FOR PREMIUM</div>
  <div class="abs display headline"><span>SEALING</span> PRODUCTS</div>

  <div class="abs display expertise">APPLICATION<br>EXPERTISE<br><b>&amp; CUSTOM<br>FABRICATION</b></div>

  <svg class="abs" style="left:110px;top:478px" width="260" height="80" viewBox="0 0 260 80">
    <polyline points="255,1 19,1 10,70 -110,70" fill="none" stroke="var(--orange-deep)" stroke-width="1.3"/>
    <line x1="151" y1="10" x2="151" y2="60" stroke="#555" stroke-width=".8"/>
  </svg>

  <div class="abs feature" style="left:138px;top:486px">
    <svg width="20" height="20" viewBox="0 0 20 20" fill="none" stroke="var(--orange)" stroke-width="1.3"><path d="M4 6a8 8 0 1 1-1 6"/><path d="M2 3v4h4"/><path d="M10 6v4l3 2"/></svg>
    <span>Reduce Time<br>to Market from<br>Weeks to Hours</span>
  </div>
  <div class="abs feature" style="left:138px;top:526px">
    <svg width="20" height="20" viewBox="0 0 20 20" fill="none" stroke="var(--orange)" stroke-width="1.3"><circle cx="11" cy="10" r="7"/><circle cx="11" cy="10" r="4"/><path d="M3 6a8 8 0 0 0 0 8"/></svg>
    <span>Eliminate Costly<br>Design Errors</span>
  </div>
  <div class="abs feature" style="left:282px;top:486px">
    <svg width="20" height="20" viewBox="0 0 20 20" fill="none" stroke="var(--orange)" stroke-width="1.3"><path d="M8 12l-2-2 6-7 5-1-1 5-7 6z"/><path d="M6 14l-3 3M9 15l-2 3M5 11l-3 2"/></svg>
    <span>Faster Time<br>to Market</span>
  </div>
  <div class="abs feature" style="left:282px;top:526px">
    <svg width="20" height="20" viewBox="0 0 20 20" fill="none" stroke="var(--orange)" stroke-width="1.3"><circle cx="10" cy="8" r="6"/><path d="M10 14v5"/><path d="M12 6h-3a1.2 1.2 0 0 0 0 2.5h2a1.2 1.2 0 0 1 0 2.5H8M10 4v8"/></svg>
    <span>Reduced R &amp;<br>D Budgets</span>
  </div>

  <div class="abs footer" style="top:559px;color:#fff">
    <span class="ic"><svg width="8" height="8" viewBox="0 0 10 10" fill="none" stroke="var(--orange)" stroke-width="1.2"><path d="M2 1l2 2-1 1.5 2.5 2.5L7 6l2 2-1.5 1.5C4 9 1 6 .5 2.5z"/></svg>555.010.4821</span>
    <span class="sep"></span>
    <span class="ic"><svg width="9" height="7" viewBox="0 0 10 8" fill="none" stroke="var(--orange)" stroke-width="1"><rect x=".5" y=".5" width="9" height="7"/><path d="M.5 .5L5 4l4.5-3.5"/></svg>info@corvane.com</span>
  </div>
  <div class="abs web" style="top:556px">www.corvane.com</div>
</section>

<!-- BACK SIDE -->
<section class="flyer flyer--back" aria-label="Flyer back">
  <div class="abs back-top"></div>
  <div class="abs display quick"><span>QUICK</span> PROTOTYPING</div>
  <div class="abs redefine">Redefine your<br><b>industry</b> with<br><b>3D printing</b></div>
  <svg class="abs" style="left:0;top:60px" width="420" height="90" viewBox="0 0 420 90">
    <polyline points="382,8 177,8 166,82 0,82" fill="none" stroke="var(--orange-deep)" stroke-width="1.3"/>
  </svg>
  <div class="abs need">NEED QUALITY PARTS?</div>
  <div class="abs need-sub">Let us print your custom<br>one-off or production pieces</div>

  <div class="abs steps">
    <div class="step"><span class="step__num">1</span><span>Send us your<br>Rubber part<br>design file</span></div>
    <div class="step"><span class="step__num">2</span><span>Recieve your<br>estimate within<br>24 hours</span></div>
    <div class="step"><span class="step__num">3</span><span>Receive your<br>prototype sample<br>within 10 days</span></div>
  </div>
  <div class="abs confirm">Confirm fitment and function before losing time and money on costly mold</div>

  <div class="abs product" style="left:148px">
    <div class="product__photo" role="img" aria-label="Photograph of black and brown rubber seals" style="background:radial-gradient(circle at 45% 45%,#7a4b33,#2b211c 60%,#bdbdbd)"></div>
    <div class="display product__name">SEALS</div>
    <div class="product__text">Custom rubber seals printed to your exact spec and tolerance.</div>
  </div>
  <div class="abs product" style="left:231px">
    <div class="product__photo" role="img" aria-label="Photograph of black rubber gaskets" style="background:radial-gradient(circle at 50% 45%,#4c4f52,#1d1e20 55%,#7fb7a8)"></div>
    <div class="display product__name">GASKETS</div>
    <div class="product__text">Flexible gaskets in any profile, from single parts to full runs.</div>
  </div>
  <div class="abs product" style="left:314px">
    <div class="product__photo" role="img" aria-label="Photograph of coloured hoses and fittings" style="background:radial-gradient(circle at 50% 50%,#e4833a,#8a3f6a 55%,#c8c8c8)"></div>
    <div class="display product__name">HOSES</div>
    <div class="product__text">Durable hose parts and fittings made in tough elastomers.</div>
  </div>

  <div class="abs benefits-band"></div>
  <div class="abs display benefits-title">BENEFITS OF 3D PRINTING</div>

  <div class="abs benefit" style="top:375px">
    <div class="benefit__label">SPEED TIME TO MARKET</div>
    <div class="benefit__desc">Go from file to finished rubber part in days, not the weeks tooling demands.</div>
    <div class="benefit__icon"><svg width="16" height="16" viewBox="0 0 16 16" fill="none" stroke="#555" stroke-width="1.6"><path d="M2 11a6 6 0 1 1 12 0"/><path d="M8 11l3-4"/></svg></div>
  </div>
  <div class="abs benefit" style="top:409px">
    <div class="benefit__label">WIN BUSINESS</div>
    <div class="benefit__desc">Quote faster and deliver samples first to win more contracts from your customers.</div>
    <div class="benefit__icon"><svg width="16" height="16" viewBox="0 0 16 16" fill="#555"><path d="M4 2h8v4a4 4 0 0 1-8 0z"/><rect x="7" y="9" width="2" height="3"/><rect x="5" y="12" width="6" height="2"/></svg></div>
  </div>
  <div class="abs benefit" style="top:443px">
    <div class="benefit__label">PERSONALISE PRODUCTS</div>
    <div class="benefit__desc">Tailor every part to your design with no minimum order or setup fees.</div>
    <div class="benefit__icon"><svg width="16" height="16" viewBox="0 0 16 16" fill="#555"><circle cx="8" cy="5" r="3"/><path d="M2 15a6 5 0 0 1 12 0z"/></svg></div>
  </div>
  <div class="abs benefit" style="top:477px">
    <div class="benefit__label">REDUCE DEVELOPMENT COST</div>
    <div class="benefit__desc">Skip costly moulds and refine designs freely before committing to production.</div>
    <div class="benefit__icon"><svg width="16" height="16" viewBox="0 0 16 16" fill="#555"><path d="M4 12a3 3 0 0 1 0-6 4 4 0 0 1 7.5-1A3.5 3.5 0 0 1 12 12z"/></svg></div>
  </div>
  <div class="abs benefit" style="top:511px">
    <div class="benefit__label">INCREASE INNOVATION</div>
    <div class="benefit__desc">Test new ideas quickly and bring better rubber products to market sooner.</div>
    <div class="benefit__icon"><svg width="16" height="16" viewBox="0 0 16 16" fill="#555"><rect x="2" y="10" width="2.5" height="4"/><rect x="6" y="8" width="2.5" height="6"/><rect x="10" y="5" width="2.5" height="9"/><path d="M2 8l5-3 3 1 4-4" stroke="#555" fill="none"/></svg></div>
  </div>

  <div class="abs footer back-footer" style="top:559px">
    <span class="ic"><svg width="8" height="8" viewBox="0 0 10 10" fill="none" stroke="var(--orange)" stroke-width="1.2"><path d="M2 1l2 2-1 1.5 2.5 2.5L7 6l2 2-1.5 1.5C4 9 1 6 .5 2.5z"/></svg>555.010.4821</span>
    <span class="sep"></span>
    <span class="ic"><svg width="9" height="7" viewBox="0 0 10 8" fill="none" stroke="var(--orange)" stroke-width="1"><rect x=".5" y=".5" width="9" height="7"/><path d="M.5 .5L5 4l4.5-3.5"/></svg>info@corvane.com</span>
  </div>
  <div class="abs web" style="top:556px">www.corvane.com</div>
</section>

</body>
</html>
```